Business Card Design For Marketing Agnecy LVP

Need business card design for marketing agency.

Doug Fenwick
President, CEO
1-555-302-4196
doug@boldpromoperksgroup.example
www.BoldPromoPerksGroup.example

Back Side:
Boost Sales Using Rewards, Incentives & Giveaways
Get A Free Sample Package

Target Market(s)

B2B

Industry/Entity Type

Marketing

Contact Information for Business Card

Doug Fenwick
President, CEO
1-555-302-4196

Back Side:
Get A Free Sample Package

Please note that my current url is OLD DESIGN. I am working on new design and want the business card to match color themes at least on new site. Here is the demo link for new site so you can see the colors I use, etc.

http://layoutcratehub.example/kq/doug/lvp_final/index.html

Requirements
Must have
• Please note that my current url is OLD DESIGN. I am working on new design and want the business card to match color themes at least on new site. Here is the demo link for new site so you can see the colors I use, etc.

Nice to have

Should not have

```html
<!DOCTYPE html>
<html lang="en">
<head>
<meta charset="utf-8">
<title>LVP Business Card</title>
<link href="https://fonts.googleapis.com/css2?family=Open+Sans:wght@400;600;700;800&display=swap" rel="stylesheet">
<style>
  :root {
    --brand-blue: #1d74bd;
    --edge-grey: #4d4f53;
    --card-white: #f7f8f9;
    --ink-white: #ffffff;
    --page-bg: #e6e8eb;
    --rule: rgba(255,255,255,0.55);
  }
  * { margin: 0; padding: 0; box-sizing: border-box; }
  html, body {
    width: 1200px; height: 900px; overflow: hidden;
    background: var(--page-bg);
    font-family: "Open Sans", Arial, sans-serif;
  }
  .card {
    position: absolute; left: 100px; top: 140px;
    width: 1000px; height: 621px;
    background: var(--card-white);
    box-shadow: 0 18px 40px rgba(0,0,0,0.18);
    overflow: hidden;
  }
  .card-wave { position: absolute; inset: 0; width: 100%; height: 100%; }
  .contact-block { position: absolute; left: 42px; top: 34px; color: var(--ink-white); }
  .person-name { font-size: 34px; font-weight: 700; letter-spacing: 0.5px; line-height: 1.1; }
  .person-title { font-size: 24px; font-weight: 400; margin-top: 2px; }
  .contact-list { list-style: none; margin-top: 28px; }
  .contact-list li {
    display: flex; align-items: center; gap: 10px;
    font-size: 25px; line-height: 37px;
  }
  .contact-list svg { width: 22px; height: 22px; flex: none; }
  .contact-rule {
    position: absolute; left: 42px; top: 271px;
    width: 472px; height: 1.5px; background: var(--rule);
  }
  .offer-list {
    position: absolute; left: 42px; top: 294px; list-style: none;
    color: var(--ink-white); font-size: 22px; font-weight: 700; line-height: 45px;
  }
  .brand-name {
    position: absolute; left: 625px; top: 310px;
    font-size: 150px; font-weight: 800; color: var(--brand-blue);
    line-height: 1; letter-spacing: 2px;
  }
</style>
</head>
<body>
  <div class="card">
    <svg class="card-wave" viewBox="0 0 652 405" preserveAspectRatio="none" aria-hidden="true">
      <path fill="var(--edge-grey)" d="M0 0 H508 C520 0 534 6 534 27 C534 40 524 48 513 51 C423 124 252 344 0 392 Z"/>
      <path fill="var(--brand-blue)" d="M0 0 H505 C516 0 530 5 530 24 C530 37 520 44 509 47 C420 120 250 338 0 386 Z"/>
    </svg>

    <div class="contact-block">
      <div class="person-name">DOUG FENWICK</div>
      <div class="person-title">President, CEO</div>
      <ul class="contact-list">
        <li>
          <svg viewBox="0 0 24 24" fill="#fff"><path d="M6.6 10.8a15 15 0 0 0 6.6 6.6l2.2-2.2c.3-.3.7-.4 1-.2 1.1.4 2.3.6 3.6.6.6 0 1 .4 1 1V20c0 .6-.4 1-1 1A17 17 0 0 1 3 4c0-.6.4-1 1-1h3.5c.6 0 1 .4 1 1 0 1.3.2 2.5.6 3.6.1.3 0 .7-.2 1z"/></svg>
          1-555-302-4196
        </li>
        <li>
          <svg viewBox="0 0 24 24" fill="#fff"><path d="M2 5h20v14H2z M4 7v.4l8 5 8-5V7l-8 5z" fill-rule="evenodd"/></svg>
          doug@boldpromoperksgroup.example
        </li>
        <li>
          <svg viewBox="0 0 24 24"><circle cx="12" cy="12" r="9.5" fill="#fff"/><path d="M5 9c3 0 4 2 3 4s1 3 2 5M13 3c0 3 3 3 4 5s3 2 4 2" stroke="var(--brand-blue)" stroke-width="1.8" fill="none"/></svg>
          www.BoldPromoPerksGroup.example
        </li>
      </ul>
    </div>
    <div class="contact-rule"></div>
    <ul class="offer-list">
      <li>BOOST SALES USING REWARDS</li>
      <li>INCENTIVES &amp; GIVEAWAYS</li>
      <li>GET A FREE SAMPLE PACKAGE</li>
    </ul>

    <span class="brand-name">LVP</span>
  </div>
</body>
</html>
```